BOLD & MINIMALIST DESIGN NEEDED

We want a very bold but minimalistic business card design that is impactful and utilizes both sides of the business card. Our current logo is included for your use.

We want bold fonts and good use of negative space. We don't want the logo to overpower the design.

Target Market(s)

Professionals who are building new commercial buildings.

Industry/Entity Type

Construction

Contact Information for Business Card

Name, Title, email, office phone, cell phone, website

Font styles to use
Serif
Sans Serif

Requirements
Must have
• Bold design!

```html
<!DOCTYPE html>
<html lang="en">
<head>
<meta charset="utf-8">
<title>Ridgeline Design + Build — Business Card</title>
<link href="https://fonts.googleapis.com/css2?family=Montserrat:wght@400;500;700;800&display=swap" rel="stylesheet">
<style>
  :root {
    --backdrop: #3b3b3b;
    --card: #1d1d1d;
    --card-deep: #161616;
    --accent: #8cc63f;
    --ink: #ffffff;
  }
  * { margin: 0; padding: 0; box-sizing: border-box; }
  html, body {
    width: 1200px; height: 791px; overflow: hidden;
    background: var(--backdrop);
    font-family: "Montserrat", sans-serif;
  }
  .stage {
    width: 1200px; height: 791px;
    display: flex; align-items: center; justify-content: center; gap: 40px;
  }
  .card {
    position: relative;
    width: 540px; height: 300px;
    background: var(--card);
    border: 2px solid var(--accent);
    overflow: hidden;
    box-shadow: 0 18px 40px rgba(0,0,0,.45);
  }

  /* front */
  .holder {
    position: absolute; top: 100px; right: 54px; text-align: right;
  }
  .holder__name {
    color: var(--accent); font-weight: 800; font-size: 19px; letter-spacing: .3px;
    text-transform: uppercase; line-height: 1.1;
  }
  .holder__title {
    color: var(--ink); font-weight: 400; font-size: 13px; margin-top: 3px;
  }
  .divider {
    position: absolute; left: 76px; right: 50px; top: 176px;
    height: 1px; background: var(--accent);
  }
  .brand {
    position: absolute; left: 60px; top: 92px;
    display: flex; align-items: center; gap: 10px;
  }
  .brand__dot {
    width: 14px; height: 14px; background: var(--accent); flex: none;
  }
  .brand__name {
    color: var(--ink); font-weight: 800; font-size: 22px; letter-spacing: 1px;
    text-transform: uppercase; line-height: 1.15;
  }
  .contact {
    position: absolute; left: 76px; top: 192px;
    list-style: none;
  }
  .contact__item {
    display: flex; align-items: center; gap: 10px;
    color: var(--ink); font-size: 12.5px; font-weight: 500; line-height: 20px;
  }
  .contact__icon { width: 12px; height: 12px; flex: none; }

  /* back */
  .card--back { background: var(--card-deep); }
  .back__pattern {
    position: absolute; inset: 0;
    background:
      radial-gradient(ellipse 60% 50% at 80% 40%, rgba(90,90,90,.45), transparent 70%),
      linear-gradient(135deg, #0e0e0e 0%, #1c1c1c 45%, #333333 100%);
  }
  .back__brand {
    position: absolute; right: 48px; top: 150px;
    display: flex; align-items: center; gap: 10px;
  }
</style>
</head>
<body>
<main class="stage">
  <section class="card card--front" aria-label="Card front">
    <div class="brand">
      <span class="brand__dot"></span>
      <span class="brand__name">Ridgeline<br>Design + Build</span>
    </div>
    <div class="holder">
      <p class="holder__name">Marcus Treadwell</p>
      <p class="holder__title">President</p>
    </div>
    <div class="divider"></div>
    <ul class="contact">
      <li class="contact__item">
        <svg class="contact__icon" viewBox="0 0 12 12"><path d="M2 1l2.5 0 1 3-1.5 1a6 6 0 0 0 3 3l1-1.5 3 1V10a1 1 0 0 1-1 1A9 9 0 0 1 1 2a1 1 0 0 1 1-1z" fill="#8cc63f"/></svg>
        555-014-2200
      </li>
      <li class="contact__item">
        <svg class="contact__icon" viewBox="0 0 12 12"><rect x="3" y="0.5" width="6" height="11" rx="1" fill="none" stroke="#8cc63f"/></svg>
        555-014-2201
      </li>
      <li class="contact__item">
        <svg class="contact__icon" viewBox="0 0 12 12"><rect x="0.5" y="2.5" width="11" height="7" fill="none" stroke="#8cc63f"/><path d="M0.5 2.5l5.5 4 5.5-4" fill="none" stroke="#8cc63f"/></svg>
        m.treadwell@rdb-build.com
      </li>
      <li class="contact__item">
        <svg class="contact__icon" viewBox="0 0 12 12"><circle cx="6" cy="6" r="5.5" fill="#8cc63f"/></svg>
        www.rdb-build.com
      </li>
    </ul>
  </section>

  <section class="card card--back" aria-label="Card back">
    <div class="back__pattern" role="img" aria-label="Repeating tone-on-tone brand mark pattern in black and dark grey"></div>
    <div class="back__brand">
      <span class="brand__dot"></span>
      <span class="brand__name">Ridgeline</span>
    </div>
  </section>
</main>
</body>
</html>
```